HVAC Design Services

I want a brochure to market my services. I own TOVEN Design Services LLC. I specialize in Mechanical Design with HVAC Design being my
specialty. I also do Plumbing and Civil Design. I have a strong resume with over 30 years experience. I was the Lead Mechanical Designer and Cad Manager for the mechanical group at an Architectural Engineering company for over 10 years.

I would like a professional looking brochure to pass out to engineering offices. I am targeting over-load work, when an office is so busy they need temporary help. Special project. Freeing up the engineer with my experience and capability to work with little to no direction .

1. HVAC Design
a) Calculate cfm
b) Layout and route ductwork
c) Size Ductwork
d) Choose and Layout grilles, registers and diffusers
e) Choose equipment and locate on plans
f) Create HVAC Floor Plans, Sections, Details and Schedules

2. Plumbing Design
a) Layout and route plumbing
b) Size piping
c) Create Plumbing Floor Plans, Sections, Details and Schedules.

3. DraftCore 3D Modeling

4. Civil and GIS experience

5. DraftCore 3D Modeling

6. Some Electrical and Structural Design experience

```html
<!DOCTYPE html>
<html lang="en">
<head>
<meta charset="utf-8">
<title>TOVEN Design Services LLC – HVAC Design Brochure</title>
<link href="https://fonts.googleapis.com/css2?family=Bebas+Neue&display=swap" rel="stylesheet">
<style>
  :root {
    --charcoal: #333333;
    --green: #62a744;
    --green-text: #5ea53f;
    --white: #ffffff;
    --band-grey: rgba(205, 205, 205, 0.88);
    --label-grey: rgba(120, 120, 120, 0.85);
    --blueprint: #2a5fb0;
    --ink: #333333;
  }
  * { margin: 0; padding: 0; box-sizing: border-box; }
  html, body { width: 1200px; height: 927px; overflow: hidden; background: var(--white); }
  .brochure { position: relative; width: 1200px; height: 927px; overflow: hidden; font-family: "Bebas Neue", sans-serif; }
  .backdrop { position: absolute; inset: 0; }
  .text { position: absolute; white-space: nowrap; line-height: 1; }

  /* Left panel */
  .wordmark { left: 0; width: 402px; text-align: center; top: 150px; font-size: 32px; letter-spacing: 1px; color: var(--white); }
  .headline { left: 0; width: 402px; text-align: center; font-size: 64px; }
  .headline.green { color: var(--green-text); }
  .headline.white { color: var(--white); }
  .band-text { left: 51px; font-size: 26px; color: var(--ink); }

  /* Middle panel */
  .experience { left: 451px; font-size: 49px; color: var(--white); }
  .section-title { font-size: 41px; }
  .hvac-title { left: 451px; top: 165px; color: var(--ink); }
  .service-list { position: absolute; list-style: none; }
  .service-list li { position: absolute; left: 0; padding-left: 20px; font-size: 26px; line-height: 30px; white-space: nowrap; }
  .service-list li::before { content: ""; position: absolute; left: 0; top: 3px; bottom: 5px; width: 6px; }
  .hvac-list { left: 451px; top: 0; }
  .hvac-list li { color: var(--white); }
  .hvac-list li::before { background: var(--charcoal); }

  /* Right panel */
  .photo-label { position: absolute; left: 883px; width: 234px; height: 33px; background: var(--label-grey); color: var(--white); font-size: 25px; line-height: 36px; text-align: center; white-space: nowrap; }
  .plumbing-title { left: 836px; top: 375px; color: var(--green-text); }
  .plumbing-list { left: 836px; top: 0; }
  .plumbing-list li { color: var(--ink); padding-left: 22px; }
  .plumbing-list li::before { background: var(--green); }
  .contact-name { left: 800px; width: 400px; text-align: center; top: 808px; font-size: 36px; letter-spacing: 4px; color: var(--green-text); }
  .contact-phone { left: 800px; width: 400px; text-align: center; top: 845px; font-size: 40px; color: var(--white); }
  .contact-role { left: 800px; width: 400px; text-align: center; top: 891px; font-size: 17px; color: var(--green-text); }
</style>
</head>
<body>
<div class="brochure">
  <svg class="backdrop" width="1200" height="927" viewBox="0 0 1200 927" xmlns="http://www.w3.org/2000/svg">
    <defs>
      <linearGradient id="houseDusk" x1="0" y1="0" x2="0" y2="1">
        <stop offset="0" stop-color="#3c5a86"/><stop offset="0.6" stop-color="#4a3b33"/><stop offset="1" stop-color="#2d3a2a"/>
      </linearGradient>
      <linearGradient id="acUnits" x1="0" y1="0" x2="0" y2="1">
        <stop offset="0" stop-color="#c9ccce"/><stop offset="0.5" stop-color="#4a4d50"/><stop offset="1" stop-color="#6b6a55"/>
      </linearGradient>
      <linearGradient id="modelHouse" x1="0" y1="0" x2="1" y2="1">
        <stop offset="0" stop-color="#dfe6ee"/><stop offset="0.5" stop-color="#a8473e"/><stop offset="1" stop-color="#e9edf1"/>
      </linearGradient>
      <linearGradient id="blueprints" x1="0" y1="0" x2="1" y2="1">
        <stop offset="0" stop-color="#b9cde3"/><stop offset="1" stop-color="#eef3f8"/>
      </linearGradient>
      <linearGradient id="pipes" x1="0" y1="0" x2="1" y2="0">
        <stop offset="0" stop-color="#7a3d2e"/><stop offset="0.6" stop-color="#9aa3a8"/><stop offset="1" stop-color="#7d4133"/>
      </linearGradient>
    </defs>

    <!-- Left panel -->
    <rect x="0" y="0" width="402" height="927" fill="var(--charcoal)"/>
    <polygon points="0,560 402,407 402,662 0,812" fill="url(#houseDusk)" role="img" aria-label="Photo of a lit timber house at dusk"/>
    <polygon points="0,812 402,662 402,680 0,836" fill="var(--green)"/>
    <polygon points="0,836 402,680 402,927 0,927" fill="var(--blueprint)" role="img" aria-label="Blueprint drawing of mechanical plans"/>
    <rect x="0" y="716" width="402" height="91" fill="var(--band-grey)"/>

    <!-- Middle panel -->
    <rect x="402" y="0" width="398" height="698" fill="var(--green)"/>
    <rect x="402" y="698" width="398" height="229" fill="url(#acUnits)" role="img" aria-label="Photo of two outdoor air conditioning condenser units"/>

    <!-- Right panel -->
    <rect x="800" y="0" width="400" height="927" fill="var(--white)"/>
    <polygon points="800,0 1200,0 1200,95 800,218" fill="url(#modelHouse)" role="img" aria-label="Photo of a 3D scale model house on drawings"/>
    <polygon points="800,218 1200,95 1200,112 800,236" fill="var(--charcoal)"/>
    <polygon points="800,236 1200,112 1200,247 800,362" fill="url(#blueprints)" role="img" aria-label="Photo of rolled construction blueprints"/>
    <polygon points="800,362 1200,247 1200,265 800,382" fill="var(--charcoal)"/>
    <polygon points="800,694 1200,553 1200,690 800,843" fill="url(#pipes)" role="img" aria-label="Photo of plumbing pipes and valves on a brick wall"/>
    <polygon points="800,843 1200,690 1200,927 800,927" fill="var(--charcoal)"/>
  </svg>

  <!-- Left panel text -->
  <div class="text wordmark">TOVEN DESIGN SERVICES LLC</div>
  <div class="text headline green" style="top:238px">OVERLOADED!</div>
  <div class="text headline green" style="top:298px">NEED A HAND?</div>
  <div class="text headline white" style="top:373px">SHORT ON STAFF</div>
  <div class="text band-text" style="top:731px">SOME ELECTRICAL AND STRUCTURAL</div>
  <div class="text band-text" style="top:766px">DESIGN EXPERIENCE</div>

  <!-- Middle panel text -->
  <div class="text experience" style="top:41px">OVER 30 YEARS</div>
  <div class="text experience" style="top:97px">EXPERIENCE</div>
  <div class="text section-title hvac-title">HVAC DESIGN</div>
  <ul class="service-list hvac-list">
    <li style="top:224px">CALCULATE CFM</li>
    <li style="top:284px">LAYOUT AND ROUTE DUCTWORK</li>
    <li style="top:345px">SIZE DUCTWORK</li>
    <li style="top:405px">CHOOSE AND LAYOUT GRILLES,<br>REGISTERS AND DIFFUSERS</li>
    <li style="top:496px">CHOOSE EQUIPMENT AND LOCATE<br>ON PLANS</li>
    <li style="top:587px">CREATE HVAC FLOOR PLANS,<br>SECTIONS, DETAILS AND<br>SCHEDULES</li>
  </ul>

  <!-- Right panel text -->
  <div class="photo-label" style="top:62px">DRAFTCORE 3D MODELING</div>
  <div class="photo-label" style="top:227px">CIVIL AND GIS EXPERIENCE</div>
  <div class="text section-title plumbing-title">PLUMBING DESIGN</div>
  <ul class="service-list plumbing-list">
    <li style="top:421px">LAYOUT AND ROUTE PLUMBING</li>
    <li style="top:481px">SIZE PIPING</li>
    <li style="top:546px; line-height:35px">CREATE PLUMBING FLOOR PLANS,<br>SECTIONS, DETAILS AND<br>SCHEDULES.</li>
  </ul>
  <div class="text contact-name">MARCO DELGADO</div>
  <div class="text contact-phone">(555)-014-2290</div>
  <div class="text contact-role">SR. MECHANICAL/CIVIL PROJECT DESIGNER</div>
</div>
</body>
</html>
```